Velvet Loom (E-commerce) Website for Embroidery shop

Briefing:

Velvet Loom is an online personalized embroidery shop targeting mainly three customer segments:
1) lovers and marring couples
2) close friends wishing to give unique gifts
3) moms with new born baby personalized gifts

These customers are being served through our three major business lines:
1) Bathrobes and towels with personalized embroidery
2) Embroidered pillows and cushions
3) baby gifts with costumed baby sets stitched

Requirements:

The business has been recently established with moderate variety of products introduced so far. The website must consists of four major pages; a home page and three pages for every single business line. All images necessary for the web design are shareable upon request for copyright reasons if necessary. Please post a few products in each page to make it easy for the employee to use as benchmarks to upload other products.

The website also should contain all items and buttons exist in any e-commerce website such as:

1- social links:
a. (Major) Instagram: https://www.instagram.com/velvet.loom.studio/
b. Twitter: https://twitter.com/Velvet_Loom_
c. Facebook: https://www.facebook.com/Velvet.loom.studio/
d. Snapchat: coming soon

2- Help:
a. Delivery & Returns (inside KSA)
I. Delivery:
- Rush: within 3 business days (SAR 90)
- Express: within 5 business days (SAR 65)
- Standard: 7-10 business days ( SAR 35)
II. Returns: We guarantee you will love our product. But if you don't like it, send it back to us within two days from delivery and we will donate it to a charity and return your money subject to our terms and conditions.

b. Contact:
- Email: Velvet.loom.studio@plumemail.net
- (Mobile) Whats-app: +966 54 312 9067 (for quick response)

d. Warranty:
for only SAR 20 per product, we will give you a lifetime warranty over our German stitches

3- Payment options:
bank transfer, visa, MasterCard and PayPal

Remarks:

- This website is mainly aimed at customers in Saudi Arabia where some contents may not appeal to people from such country and results in your participation being excluded from the contest.

- You are the expert and if I am a webdesigner, I would have not posted this contest, so please use your our own judgment and creativity to come up with the best experience possible.

- Use our Instagram account as your first reference to understand our business as it is our major channel that has been used to reach our customers. Please don't use the pictures with poor quality as we will be replacing them with other images with better quality.

- We intend to have this website bilingual (i.e English and Arabic), so if you can translate it into Arabic, then we will pay you an extra $100 in addition to the contest price.

- If in doubt, please feel free to ask any question and suggestions are always encouraged and warm welcomed.

- If you succeed in this contest, you will be chosen as our ultimate Web designer. That means you will have a long relationship providing services to our customers under one of our businesses that aims at preparing start-up companies establishing their business.

Target Market(s)

1) lovers and marrying couples

Industry/Entity Type

Embroidery

Number of Pages Required

4 page

Font styles to use
Serif
Script

Colors

Designer to choose colors to be used in the design.

Requirements
Must have
• Requirements:
• The business has been recently established with moderate variety of products introduced so far. The website must consists of four major pages; a home page and three pages for every single business line. All images necessary for the web design are shareable upon request for copyright reasons if necessary. Please post a few products in each page to make it easy for the employee to use as benchmarks to upload other products.
• The Website must be also mobile use friendly!!!
• The website also should contain all items and buttons exist in any e-commerce website such as:
• 1- social links:
• a. (Major) Instagram: https://www.instagram.com/velvet.loom.studio/
• b. Twitter: https://twitter.com/Velvet_Loom_
• c. Facebook: https://www.facebook.com/Velvet.loom.studio/
• d. Snapchat: coming soon
• 2- Help:
• a. Delivery & Returns (inside KSA)
• I. Delivery:
• - Rush: within 3 business days (SAR 90)
• - Express: within 5 business days (SAR 65)
• - Standard: 7-10 business days ( SAR 35)
• II. Returns: We guarantee you will love our product. But if you don't like it, send it back to us within two days from delivery and we will donate it to a charity and return your money subject to our terms and conditions.
• b. Contact:
• - Email: Velvet.loom.studio@plumemail.net
• - (Mobile) Whats-app: +966 54 312 9067 (for quick response)
• d. Warranty:
• for only SAR 20 per product, we will give you a lifetime warranty over our German stitches
• 3- Payment options:
• bank transfer, visa, MasterCard and PayPal
• Note: You will be responsible to upload the design to the website fully and ensure its integration and functionality.

```html
<!DOCTYPE html>
<html lang="en">
<head>
<meta charset="utf-8">
<title>Velvet Loom — Embroidery Shop</title>
<link href="https://fonts.googleapis.com/css2?family=Open+Sans:wght@400;600;700&family=Roboto+Condensed:wght@400;700&family=Roboto+Slab:wght@400;700&display=swap" rel="stylesheet">
<style>
:root{
  --gold:#b68d45;
  --gold-dark:#9c7637;
  --ink:#222;
  --text:#555;
  --muted:#888;
  --line:#e3e3e3;
  --topbar:#3b3b3b;
  --soft:#f5f5f5;
  --white:#fff;
}
*{box-sizing:border-box;margin:0;padding:0}
html,body{width:1200px;height:2560px;overflow:hidden}
body{background:var(--white);font-family:"Open Sans",sans-serif;color:var(--text);position:relative}
.wrap{width:938px;margin:0 auto;position:relative}
svg{display:block}

/* top bar */
.topbar{height:31px;background:var(--topbar);color:#eee;font-size:11px}
.topbar .wrap{display:flex;justify-content:space-between;align-items:center;height:31px}
.topbar .group{display:flex;gap:28px;align-items:center}
.topbar .item{display:flex;align-items:center;gap:7px;text-transform:none}
.topbar .right .item{text-transform:uppercase;font-weight:700;font-size:10px;letter-spacing:.3px}

/* header */
.header{height:131px}
.logo{position:absolute;left:0;top:36px;display:flex;align-items:center;gap:10px;font-family:"Roboto Slab",serif;font-weight:700;font-size:30px;color:var(--gold)}
.logo-dot{width:18px;height:18px;border-radius:50%;background:var(--gold)}
.search{position:absolute;left:398px;top:29px;display:flex;height:33px;border:1px solid #ddd}
.search .cat{width:70px;display:flex;align-items:center;justify-content:space-between;padding:0 10px 0 14px;font-size:10px;color:var(--muted);border-right:1px solid #ddd}
.search .field{width:208px;display:flex;align-items:center;padding-left:14px;font-size:10px;color:#aaa;text-transform:uppercase}
.search .btn{width:66px;background:var(--gold);color:#fff;font-size:10px;font-weight:700;display:flex;align-items:center;justify-content:center}
.cart{position:absolute;left:757px;top:29px;width:181px;height:33px;background:#f0f0f0;display:flex;align-items:center}
.cart .icon{width:40px;height:33px;background:var(--gold);display:flex;align-items:center;justify-content:center;position:relative}
.cart .badge{position:absolute;top:-8px;left:22px;width:16px;height:16px;border-radius:50%;background:#333;color:#fff;font-size:9px;display:flex;align-items:center;justify-content:center}
.cart .label{margin-left:14px;font-size:10px;font-weight:700;color:#444}
.cart .amount{margin-left:6px;color:var(--gold);font-weight:700;font-size:13px}
.nav{position:absolute;right:0;top:87px;display:flex;gap:43px;font-size:11.5px;color:#333;text-transform:uppercase}

/* hero */
.hero{height:500px;position:relative;background:linear-gradient(110deg,#8c8683 0%,#9e9894 45%,#a9a39d 100%)}
.hero-photo{position:absolute;left:0;top:0;width:760px;height:500px;background:radial-gradient(ellipse at 40% 55%,#e6e1dc 0%,#c8c1bb 35%,#8b7d93 60%,rgba(140,134,131,0) 80%)}
.hero-copy{position:absolute;left:768px;top:130px;color:#fff}
.hero-copy h1{font-family:"Roboto Condensed",sans-serif;font-weight:700;font-size:40px;letter-spacing:.5px}
.hero-copy .offer{font-family:"Roboto Condensed",sans-serif;font-size:22px;margin-top:8px}
.hero-copy .offer b{font-size:40px}
.hero-copy p{font-size:13px;line-height:24px;width:310px;margin-top:18px;color:#f4f4f4}
.hero-copy .cta{display:inline-block;margin-top:26px;border:2px solid #d8bf8c;background:var(--gold);color:#fff;font-size:12px;font-weight:700;padding:9px 12px}
.dots{position:absolute;left:990px;top:598px;display:flex;gap:25px}
.dots span{width:14px;height:14px;border-radius:50%;border:2px solid #e0ddd9}
.dots span.on{border-color:var(--gold)}

/* segments */
.segments{display:flex;gap:9px;margin-top:10px}
.segment{width:307px;height:212px;position:relative}
.segment .label{position:absolute;left:0;top:80px;background:rgba(182,141,69,.75);color:#fff;font-family:"Roboto Slab",serif;font-weight:700;font-size:14px;padding:10px 12px;line-height:28px}
.seg-couples{background:linear-gradient(135deg,#5a3b2a,#b38a63 55%,#e6d7c4)}
.seg-friends{background:linear-gradient(135deg,#6a4a40,#3e7a3f 50%,#b52c2c)}
.seg-baby{background:linear-gradient(135deg,#4f6678,#8aa0b0 50%,#6d4d35)}

/* welcome */
.welcome{text-align:center;margin-top:38px}
.welcome h2{font-family:"Roboto Condensed",sans-serif;font-weight:400;font-size:25px;color:var(--ink)}
.welcome p{font-size:12px;line-height:24px;width:800px;margin:12px auto 0;color:var(--text)}
.divider{margin-top:40px;height:1px;background:var(--line);position:relative}
.divider span{position:absolute;left:461px;top:-3px;width:16px;height:6px;background:#fff;border:1px solid var(--line);border-radius:3px}

/* products */
.products{padding-top:42px}
.products.alt{background:var(--soft);margin-top:57px;padding-top:62px;height:483px}
.section-head{display:flex;justify-content:space-between;align-items:center}
.section-head h3{font-family:"Roboto Condensed",sans-serif;font-weight:400;font-size:24px;color:var(--ink)}
.arrows{display:flex;gap:6px}
.arrows span{width:16px;height:16px;border-radius:50%;border:1.5px solid #888;display:flex;align-items:center;justify-content:center}
.arrows span.dark{background:#333;border-color:#333}
.underline{width:70px;height:3px;background:var(--gold);margin-top:12px}
.grid{display:flex;gap:25px;margin-top:33px}
.card{width:216px;height:334px;border:1px solid #e6e6e6;background:#fff}
.card .photo{height:167px}
.card .body{padding:14px 13px}
.card h4{font-family:"Roboto Condensed",sans-serif;font-weight:400;font-size:15px;color:var(--ink)}
.card p{font-size:10.5px;line-height:20px;margin-top:6px;color:var(--text)}
.price{display:flex;align-items:center;gap:10px;margin-top:8px}
.price b{color:var(--gold);font-size:13px}
.stars{color:#c7a66a;font-size:9px;letter-spacing:1px}
.shop{display:inline-block;margin-top:12px;background:var(--gold);color:#fff;font-size:9px;font-weight:700;padding:8px 13px;border-radius:14px}
.ph1{background:linear-gradient(135deg,#8a7060,#d9cfc4 50%,#a8262a)}
.ph2{background:linear-gradient(135deg,#6d6864,#e9e4de 50%,#9b8a7a)}
.ph3{background:linear-gradient(135deg,#6f6a70,#e8e5ea 45%,#223a6a)}
.ph4{background:linear-gradient(135deg,#d46f74,#f1a3a8 50%,#6fa7c8)}
.ph5{background:linear-gradient(135deg,#6c6c70,#8c8c90 50%,#9ed0e6)}
.ph6{background:linear-gradient(135deg,#c8b59c,#eee7de 45%,#c9302e)}
.ph7{background:linear-gradient(135deg,#efeae4,#d9d1c8 45%,#6d9bd1)}
.ph8{background:linear-gradient(135deg,#8d8478,#ebe8e3 50%,#7a6d5e)}

/* service band */
.services{height:133px;background:var(--gold);margin-top:34px}
.services .wrap{display:flex;height:133px;align-items:center}
.service{flex:1;display:flex;gap:14px;padding-left:0;color:#fff}
.service + .service{border-left:1px solid rgba(255,255,255,.35);padding-left:42px}
.service h5{font-size:12px;font-weight:700;text-transform:uppercase;margin-top:2px}
.service p{font-size:11px;line-height:20px;margin-top:4px;width:230px}

/* newsletter */
.newsletter{height:95px}
.newsletter .wrap{display:flex;align-items:center;height:95px}
.newsletter .lead{font-size:11px;font-weight:700;color:#444;text-transform:uppercase}
.newsletter .email{margin-left:12px;width:255px;height:31px;border:1px solid #ddd;border-radius:16px;font-size:10px;color:#999;display:flex;align-items:center;padding-left:16px}
.newsletter .subscribe{margin-left:6px;background:var(--gold);color:#fff;font-size:10px;font-weight:700;padding:9px 15px;border-radius:16px;text-transform:uppercase}
.socials{margin-left:auto;display:flex;gap:6px}
.socials span{width:26px;height:26px;border-radius:50%}

/* footer */
.footer{height:206px;border-top:2px solid #e8e8e8;background:#fcfcfc}
.footer .wrap{display:flex;padding-top:28px}
.footer .brand{width:220px;padding-top:18px;display:flex;align-items:flex-start;gap:10px;font-family:"Roboto Slab",serif;font-weight:700;font-size:26px;color:var(--gold);border-right:1px solid var(--line);height:150px}
.footer .col{padding-left:58px;border-right:1px solid var(--line);height:150px}
.footer .col.links{width:192px}
.footer .col.account{width:233px}
.footer .col.contact{border-right:none;padding-left:70px}
.footer h6{font-family:"Roboto Condensed",sans-serif;font-weight:400;font-size:14px;color:var(--ink);margin-bottom:12px}
.footer li{list-style:none;font-size:10.5px;line-height:21px;color:var(--text)}
.contact-row{display:flex;gap:14px;font-size:10.5px;line-height:19px;margin-bottom:12px;width:230px}
.contact-row a{color:var(--text)}
.copyright{height:50px;border-top:1px solid var(--line);text-align:center;font-size:10.5px;color:var(--text);padding-top:18px}
</style>
</head>
<body>

<div class="topbar">
  <div class="wrap">
    <div class="group">
      <span class="item">
        <svg width="11" height="11" viewBox="0 0 24 24"><path fill="#eee" d="M6.6 10.8a15 15 0 006.6 6.6l2.2-2.2a1 1 0 011-.25 11.4 11.4 0 003.6.6 1 1 0 011 1V20a1 1 0 01-1 1A17 17 0 013 4a1 1 0 011-1h3.5a1 1 0 011 1c0 1.25.2 2.45.6 3.6a1 1 0 01-.25 1z"/></svg>
        Mobile : +966 54 312 9067
      </span>
      <span class="item">
        <svg width="12" height="10" viewBox="0 0 24 18"><rect x="1" y="1" width="22" height="16" fill="#eee"/><path d="M1 1l11 9 11-9" stroke="#3b3b3b" stroke-width="2" fill="none"/></svg>
        Email: Velvet.loom.studio@plumemail.net
      </span>
    </div>
    <div class="group right">
      <span class="item"><svg width="9" height="11" viewBox="0 0 18 22"><rect x="1" y="9" width="16" height="12" fill="#eee"/><path d="M4 9V6a5 5 0 0110 0v3" stroke="#eee" stroke-width="2.5" fill="none"/></svg>Register</span>
      <span class="item"><svg width="10" height="10" viewBox="0 0 20 20"><rect x="1" y="3" width="15" height="16" stroke="#eee" stroke-width="2" fill="none"/><path d="M9 11L18 2" stroke="#eee" stroke-width="2.5"/></svg>Request Quote</span>
      <span class="item">English <svg width="7" height="5" viewBox="0 0 10 6"><path d="M1 1l4 4 4-4" stroke="#eee" stroke-width="1.5" fill="none"/></svg></span>
    </div>
  </div>
</div>

<header class="header">
  <div class="wrap">
    <div class="logo"><span class="logo-dot"></span>Velvet Loom</div>
    <div class="search">
      <div class="cat">ALL <svg width="8" height="5" viewBox="0 0 10 6"><path d="M0 0h10L5 6z" fill="#999"/></svg></div>
      <div class="field">Search products</div>
      <div class="btn">SEARCH</div>
    </div>
    <div class="cart">
      <div class="icon">
        <svg width="20" height="17" viewBox="0 0 24 20"><path d="M1 2h4l3 11h12l3-8H7" stroke="#fff" stroke-width="2.2" fill="none"/><circle cx="9" cy="17" r="2" fill="#fff"/><circle cx="19" cy="17" r="2" fill="#fff"/></svg>
        <span class="badge">0</span>
      </div>
      <span class="label">MY CART</span><span class="amount">$0.00</span>
    </div>
    <nav class="nav">
      <span>Home</span><span>About Us</span><span>Services</span><span>Products</span><span>Testimonials</span><span>Blog</span><span>Contact Us</span>
    </nav>
  </div>
</header>

<section class="hero">
  <div class="hero-photo" role="img" aria-label="Purple and white towels with embroidered monogram and name, tied with purple satin ribbons"></div>
  <div class="hero-copy">
    <h1>EMBROIDERY SHOP</h1>
    <div class="offer">UPTO <b>20%</b> OFFER</div>
    <p>Adipiscing elit, sed do eiusmod tempor incididunt ut labore et dolore magna aliqua...</p>
    <span class="cta">SHOP NOW TODAY</span>
  </div>
  <div class="dots"><span class="on"></span><span></span><span></span></div>
</section>

<div class="wrap">
  <div class="segments">
    <div class="segment seg-couples" role="img" aria-label="Couple sitting together at a table">
      <div class="label">Lovers and Marring Couples</div>
    </div>
    <div class="segment seg-friends" role="img" aria-label="Hands exchanging a wrapped gift box">
      <div class="label">Close Friends Wishing to<br>Give Unique Gifts</div>
    </div>
    <div class="segment seg-baby" role="img" aria-label="Newborn baby sleeping in a knitted hat beside a teddy bear">
      <div class="label">Moms With New Born Baby<br>Personalized Gifts</div>
    </div>
  </div>

  <div class="welcome">
    <h2>Welcome to Velvet Loom</h2>
    <p>Lorem ipsum dolor sit amet, consectetur adipiscing elit, sed do eiusmod tempor incididunt ut labore et dolore magna aliqua. Ut enim ad minim veniam, quis nostrud exercitation ullamco laboris nisi ut aliquip ex ea commodo consequat. Duis aute irure dolor in reprehenderit in voluptate velit esse cillum dolore eu fugiat nulla pariatur. Excepteur sint occaecat cupidatat...</p>
  </div>
  <div class="divider"><span></span></div>
</div>

<section class="products">
  <div class="wrap">
    <div class="section-head">
      <h3>Featured Products</h3>
      <div class="arrows">
        <span><svg width="8" height="8" viewBox="0 0 10 10"><path d="M8 5H2M5 2L2 5l3 3" stroke="#888" stroke-width="1.5" fill="none"/></svg></span>
        <span class="dark"><svg width="8" height="8" viewBox="0 0 10 10"><path d="M2 5h6M5 2l3 3-3 3" stroke="#fff" stroke-width="1.5" fill="none"/></svg></span>
      </div>
    </div>
    <div class="underline"></div>
    <div class="grid">
      <div class="card"><div class="photo ph1" role="img" aria-label="Embroidered towel set with names in red and cream"></div><div class="body"><h4>Tempor Incididunt</h4><p>Aliquip ex ea commodo consequat.<br>Duis aute irure doloreuse...</p><div class="price"><b>$23.00</b><span class="stars">★★★★★</span></div><span class="shop">SHOP NOW</span></div></div>
      <div class="card"><div class="photo ph2" role="img" aria-label="Embroidered calendar keepsake pillow"></div><div class="body"><h4>Tempor Incididunt</h4><p>Aliquip ex ea commodo consequat.<br>Duis aute irure doloreuse...</p><div class="price"><b>$13.00</b><span class="stars">★★★★★</span></div><span class="shop">SHOP NOW</span></div></div>
      <div class="card"><div class="photo ph3" role="img" aria-label="Pair of monogrammed bathrobes in white and navy"></div><div class="body"><h4>Tempor Incididunt</h4><p>Aliquip ex ea commodo consequat.<br>Duis aute irure doloreuse...</p><div class="price"><b>$45.00</b><span class="stars">★★★★★</span></div><span class="shop">SHOP NOW</span></div></div>
      <div class="card"><div class="photo ph4" role="img" aria-label="Pink and blue towels with embroidered names"></div><div class="body"><h4>Tempor Incididunt</h4><p>Aliquip ex ea commodo consequat.<br>Duis aute irure doloreuse...</p><div class="price"><b>$34.00</b><span class="stars">★★★★★</span></div><span class="shop">SHOP NOW</span></div></div>
    </div>
  </div>
</section>

<section class="products alt">
  <div class="wrap">
    <div class="section-head">
      <h3>Top Sellings Products</h3>
      <div class="arrows">
        <span><svg width="8" height="8" viewBox="0 0 10 10"><path d="M8 5H2M5 2L2 5l3 3" stroke="#888" stroke-width="1.5" fill="none"/></svg></span>
        <span class="dark"><svg width="8" height="8" viewBox="0 0 10 10"><path d="M2 5h6M5 2l3 3-3 3" stroke="#fff" stroke-width="1.5" fill="none"/></svg></span>
      </div>
    </div>
    <div class="underline"></div>
    <div class="grid">
      <div class="card"><div class="photo ph5" role="img" aria-label="Grey towel with light blue embroidered name and ribbon"></div><div class="body"><h4>Tempor Incididunt</h4><p>Aliquip ex ea commodo consequat.<br>Duis aute irure doloreuse...</p><div class="price"><b>$23.00</b><span class="stars">★★★★★</span></div><span class="shop">SHOP NOW</span></div></div>
      <div class="card"><div class="photo ph6" role="img" aria-label="Cream and red towel set with embroidered names"></div><div class="body"><h4>Tempor Incididunt</h4><p>Aliquip ex ea commodo consequat.<br>Duis aute irure doloreuse...</p><div class="price"><b>$32.00</b><span class="stars">★★★★★</span></div><span class="shop">SHOP NOW</span></div></div>
      <div class="card"><div class="photo ph7" role="img" aria-label="White and blue towels with embroidered names and bows"></div><div class="body"><h4>Tempor Incididunt</h4><p>Aliquip ex ea commodo consequat.<br>Duis aute irure doloreuse...</p><div class="price"><b>$31.00</b><span class="stars">★★★★★</span></div><span class="shop">SHOP NOW</span></div></div>
      <div class="card"><div class="photo ph8" role="img" aria-label="White cushion with embroidered baby message"></div><div class="body"><h4>Tempor Incididunt</h4><p>Aliquip ex ea commodo consequat.<br>Duis aute irure doloreuse...</p><div class="price"><b>$23.00</b><span class="stars">★★★★★</span></div><span class="shop">SHOP NOW</span></div></div>
    </div>
  </div>
</section>

<section class="services">
  <div class="wrap">
    <div class="service">
      <svg width="30" height="22" viewBox="0 0 30 22"><rect x="1" y="3" width="17" height="12" fill="#fff"/><path d="M18 7h6l4 4v4H18z" fill="#fff"/><circle cx="7" cy="17" r="3" fill="#fff" stroke="#b68d45" stroke-width="1.5"/><circle cx="23" cy="17" r="3" fill="#fff" stroke="#b68d45" stroke-width="1.5"/></svg>
      <div><h5>Delivery</h5><p>Lorem ipsum dolor sit amet, consectetur adipiscing elit, sed do eiusmod...</p></div>
    </div>
    <div class="service">
      <svg width="20" height="20" viewBox="0 0 24 24"><path fill="#fff" d="M6.6 10.8a15 15 0 006.6 6.6l2.2-2.2a1 1 0 011-.25 11.4 11.4 0 003.6.6 1 1 0 011 1V20a1 1 0 01-1 1A17 17 0 013 4a1 1 0 011-1h3.5a1 1 0 011 1c0 1.25.2 2.45.6 3.6a1 1 0 01-.25 1z"/></svg>
      <div><h5>Call Us</h5><p>Lorem ipsum dolor sit amet, consectetur adipiscing elit, sed do eiusmod...</p></div>
    </div>
    <div class="service">
      <svg width="28" height="20" viewBox="0 0 28 20"><rect x="2" y="2" width="24" height="16" rx="3" stroke="#fff" stroke-width="2.2" fill="none"/><rect x="2" y="7" width="24" height="3" fill="#fff"/></svg>
      <div><h5>Secure Payments</h5><p>Lorem ipsum dolor sit amet, consectetur adipiscing elit, sed do eiusmod...</p></div>
    </div>
  </div>
</section>

<section class="newsletter">
  <div class="wrap">
    <span class="lead">Get our recent updates through your email id :</span>
    <span class="email">Enter your email id :</span>
    <span class="subscribe">Subscribe Now</span>
    <div class="socials">
      <span style="background:#3b5998"></span>
      <span style="background:#3aa4dc"></span>
      <span style="background:#cb2027"></span>
      <span style="background:#333"></span>
    </div>
  </div>
</section>

<footer class="footer">
  <div class="wrap">
    <div class="brand"><span class="logo-dot"></span>Velvet Loom</div>
    <div class="col links">
      <h6>Extras</h6>
      <ul><li>Specials</li><li>New products</li><li>Top sellers</li><li>Our stores</li><li>Contact us</li><li>About us</li></ul>
    </div>
    <div class="col account">
      <h6>My Account</h6>
      <ul><li>Delivery Information</li><li>Privacy Policy</li><li>Returns Policy</li><li>Terms and Conditions</li><li>FAQs</li></ul>
    </div>
    <div class="col contact">
      <h6>Contact Info</h6>
      <div class="contact-row"><svg width="10" height="14" viewBox="0 0 12 16"><path d="M6 0a6 6 0 00-6 6c0 4.5 6 10 6 10s6-5.5 6-10a6 6 0 00-6-6z" fill="#666"/><circle cx="6" cy="6" r="2" fill="#fff"/></svg><span>Latin literature from 45 BC, making over 2000 years old.</span></div>
      <div class="contact-row"><svg width="11" height="11" viewBox="0 0 24 24"><path fill="#666" d="M6.6 10.8a15 15 0 006.6 6.6l2.2-2.2a1 1 0 011-.25 11.4 11.4 0 003.6.6 1 1 0 011 1V20a1 1 0 01-1 1A17 17 0 013 4a1 1 0 011-1h3.5a1 1 0 011 1c0 1.25.2 2.45.6 3.6a1 1 0 01-.25 1z"/></svg><span>Phone :+966 54 312 9067</span></div>
      <div class="contact-row"><svg width="12" height="10" viewBox="0 0 24 18"><rect x="1" y="1" width="22" height="16" fill="#666"/><path d="M1 1l11 9 11-9" stroke="#fff" stroke-width="2" fill="none"/></svg><a>Velvet.loom.studio@plumemail.net</a></div>
    </div>
  </div>
</footer>
<div class="copyright">Copyrights © 2017, Velvet Loom. All Rights Reserved</div>

</body>
</html>
```